QRV Advisors needs a web site

We need a web site for www.qrvadvisors-example.com. QRV is a mergers and acquisition consulting company that focuses our buyer and seller services on logistics companies. We help put companies together, and help with legal and financial due diligence. We want the web site to express our service and show the logistics components. We want personalized images versus pictures of trucks and airplanes.

Our new logo uses Burgandy and grey colors. Image attached. We are not in to bold, big letters...classy, artistic, low key preferred. Confidentiality, experience, professional are what we want to express on the site.

All we expect for the first part of this project is a home page, and one subpage.  We are budgeting other funds for the technical aspects of the web site

Reason: All that I'm seeing so far is trucks, forklifts and planes. We are a legal mergers and acquisitions firm that focus on logistics. I like some of the images to say logistics, but really want it say legal, financial, and putting companies together. Will pay extra for the sub page if someone can impress us with a home page.

Reason: Swamped with another project at the moment...will work on this over the weekend and provide designer feedback and select final design by Tuesday

```html
<!DOCTYPE html>
<html lang="en">
<head>
<meta charset="utf-8">
<title>QRV Advisors — Home</title>
<link href="https://fonts.googleapis.com/css2?family=Ubuntu:wght@300;400;500;700&display=swap" rel="stylesheet">
<style>
:root{
  --burgundy:#a20c36;
  --burgundy-dark:#7d0a2a;
  --slate:#58585a;
  --slate-dark:#3c3c3e;
  --ink:#333;
  --muted:#555;
  --page:#f3f3f3;
  --line:#c9c9c9;
  --white:#fff;
}
*{box-sizing:border-box;margin:0;padding:0}
html,body{width:1028px;height:1200px;overflow:hidden}
body{font-family:'Ubuntu',sans-serif;color:var(--ink);background:var(--page);position:relative}
.abs{position:absolute}

/* Header */
.topbar{left:0;top:0;width:1028px;height:6px;background:#555}
.header{left:0;top:6px;width:1028px;height:120px;background:linear-gradient(#fafafa,#e6e6e6);border-bottom:1px solid #bbb}
.brand{left:120px;top:44px;display:flex;align-items:center;gap:10px}
.brand-mark{font-size:40px;font-weight:300;color:var(--slate-dark);letter-spacing:3px;line-height:1}
.brand-rule{width:2px;height:44px;background:var(--slate)}
.brand-name{font-size:15px;font-weight:300;color:var(--slate-dark);line-height:15px;letter-spacing:1px;text-transform:uppercase}
.social-top{left:648px;top:22px;display:flex;gap:10px}
.social-top span{width:30px;height:30px;border-radius:50%;background:linear-gradient(#6a6a6a,#2e2e2e);display:block}
.callus{left:776px;top:22px;display:flex;align-items:center;gap:6px}
.callus small{display:block;font-size:10px;color:var(--muted)}
.callus strong{display:block;font-size:16px;font-weight:400;color:var(--ink)}
.nav{top:75px;left:0;width:1028px;height:28px}
.nav a{position:absolute;top:0;height:28px;line-height:28px;font-size:9.5px;color:var(--muted);text-decoration:none;text-align:center;border-top:1px solid #b5b5b5;border-bottom:1px solid #b5b5b5}
.nav a.current{font-weight:700;color:var(--ink)}
.nav a.current::before{content:"";position:absolute;left:50%;top:0;margin-left:-4px;border:4px solid transparent;border-top-color:#333}

/* Hero */
.hero{left:0;top:126px;width:1028px;height:406px;background:#e8e8e8;overflow:hidden}
.slide{top:0;height:406px}
.slide-fleet{left:0;width:340px;background:linear-gradient(160deg,#1a1a1a,#6c6e72 60%,#4a4c50)}
.slide-deal{left:345px;width:339px;background:linear-gradient(#2c4f98,#6d8fc8 45%,#c9d5e6 70%,#e9edf2)}
.slide-team{left:688px;width:340px;background:linear-gradient(150deg,#e9e4dc,#8ea3bd 55%,#4e6680)}
.hero-caption{left:345px;top:229px;width:339px;height:177px;background:linear-gradient(rgba(255,255,255,.55),rgba(255,255,255,.9))}
.hero-caption h1{position:absolute;left:0;top:134px;width:339px;transform:translateY(-100%);text-align:center;font-size:23.5px;font-weight:700;color:var(--ink);line-height:30px;padding:0 12px}
.hero-curve{left:0;top:126px}
.dots{left:472px;top:500px;display:flex;gap:8px}
.dots span{width:15px;height:13px;background:var(--slate)}
.dots span.on{background:var(--burgundy)}

/* Services */
.section-title{top:522px;left:0;width:1028px;text-align:center;font-size:24px;color:var(--burgundy);font-weight:400}
.title-rule{top:537px;height:1px;width:220px;background:#bdbdbd}
.service{top:563px;width:238px;height:147px;background:var(--white);box-shadow:0 1px 4px rgba(0,0,0,.18)}
.service-head{height:91px;background:var(--slate);position:relative}
.service-head.accent{background:var(--burgundy)}
.service-head h2{position:absolute;left:11px;bottom:6px;font-size:19px;font-weight:400;color:var(--white);line-height:23px}
.service-head svg{position:absolute;right:10px;bottom:0}
.service p{font-size:9.8px;color:var(--muted);line-height:14.5px;padding:5px 9px 0 9px}
.band-shadow{left:0;top:726px;width:1028px;height:14px;background:radial-gradient(ellipse at center,rgba(0,0,0,.12),rgba(0,0,0,0) 70%)}

/* Info boxes */
.panel{top:760px;width:244px;height:232px;background:linear-gradient(#fff 70%,#e7e7e7);border-radius:6px 6px 0 0;box-shadow:0 6px 6px -4px rgba(0,60,90,.35)}
.panel-head{position:absolute;left:-4px;top:12px;width:252px;height:32px;background:var(--slate);color:var(--white);display:flex;align-items:center;gap:9px;padding-left:12px;font-size:16.5px;font-weight:400;letter-spacing:.5px;box-shadow:0 3px 3px rgba(0,0,0,.25)}
.more{position:absolute;right:12px;bottom:10px;font-size:9.5px;font-weight:500;color:var(--ink)}
.about-photo{position:absolute;left:11px;top:60px;width:227px;height:86px;background:linear-gradient(90deg,#c8ccd4,#e9ebef 50%,#b9c0cc)}
.about-text{position:absolute;left:15px;top:150px;width:220px;font-size:9.2px;line-height:12.3px;color:var(--muted);letter-spacing:.2px}
.news-item{position:absolute;left:12px;width:226px;display:flex;gap:9px}
.date{width:31px;flex:none;text-align:center;box-shadow:0 1px 2px rgba(0,0,0,.25)}
.date b{display:block;background:var(--burgundy);color:var(--white);font-size:11px;font-weight:500;height:16px;line-height:16px}
.date i{display:block;font-style:normal;background:#f4f4f4;font-size:9.5px;font-weight:700;height:15px;line-height:15px}
.news-item p{font-size:8.8px;line-height:12px;color:var(--muted)}
.news-item p strong{color:#222;font-weight:500}
.field{position:absolute;left:12px;width:226px;height:20px;border:1px solid #c4c4c4;border-radius:2px;background:#fff;font-size:10px;color:#666;padding:3px 8px;box-shadow:inset 0 1px 2px rgba(0,0,0,.1)}
.submit{position:absolute;left:14px;top:202px;width:56px;height:20px;background:var(--burgundy);color:var(--white);font-size:11.5px;font-weight:700;text-align:center;line-height:20px}

/* Footer */
.footer{left:0;top:1018px;width:1028px;height:182px;background:var(--burgundy);border-top:3px solid #222;color:var(--white)}
.footer h3{position:absolute;font-size:14.5px;font-weight:400}
.f-rule{position:absolute;height:0;border-top:1px dotted rgba(255,255,255,.7)}
.f-divider{position:absolute;top:20px;width:1px;height:111px;background:rgba(255,255,255,.45)}
.quick-links{position:absolute;left:118px;top:60px;list-style:none}
.quick-links li{font-size:9.8px;line-height:14.3px;padding-left:13px;position:relative}
.quick-links li::before{content:"›";position:absolute;left:0;top:-1px;font-size:11px}
.map{position:absolute;left:288px;top:47px;width:184px;height:80px;background:linear-gradient(135deg,#efece4,#e2ded4);border:2px solid #fff}
.contact-row{position:absolute;left:480px;display:flex;gap:9px;align-items:flex-start;font-size:10px;line-height:15px}
.contact-row svg{flex:none}
.footer-mark{position:absolute;left:730px;top:18px;width:178px;text-align:center;font-size:54px;font-weight:300;letter-spacing:10px;line-height:60px}
.social-foot{position:absolute;left:764px;top:116px;display:flex;gap:10px}
.social-foot span{width:30px;height:30px;border-radius:5px;background:rgba(255,255,255,.25);display:block}
.copyright{position:absolute;left:0;top:156px;width:1028px;text-align:center;font-size:12px}
</style>
</head>
<body>

<div class="abs topbar"></div>
<header class="abs header"></header>
<div class="abs brand">
  <span class="brand-mark">QRV</span>
  <span class="brand-rule"></span>
  <span class="brand-name">QRV<br>Advisors</span>
</div>
<div class="abs social-top" aria-label="Social links"><span></span><span></span><span></span></div>
<div class="abs callus">
  <svg width="28" height="28" viewBox="0 0 28 28"><circle cx="14" cy="14" r="12.5" fill="none" stroke="#a20c36" stroke-width="1.6"/><path d="M10 8c-1 1-1.5 2.5-.5 5s3 4.8 5.5 6c1.5.7 2.8.3 3.8-.8l-2.3-2.2-1.6 1c-1.5-.8-2.8-2.2-3.5-3.7l1-1.6z" fill="#a20c36"/></svg>
  <div><small>Call Us Today</small><strong>123 456 7890</strong></div>
</div>
<nav class="abs nav">
  <a class="current" style="left:380px;width:38px">HOME</a>
  <a style="left:433px;width:65px">ABOUT US</a>
  <a style="left:509px;width:83px">BUYER SERVICES</a>
  <a style="left:604px;width:84px">SELLER SERVICES</a>
  <a style="left:700px;width:80px">NEWS &amp; EVENTS</a>
  <a style="left:792px;width:40px">FAQ's</a>
  <a style="left:845px;width:64px">CONTACT</a>
</nav>

<section class="abs hero">
  <div class="abs slide slide-fleet" role="img" aria-label="Aircraft, truck and vans on a dark floor"></div>
  <div class="abs slide slide-deal" role="img" aria-label="Business handshake in front of office towers"></div>
  <div class="abs slide slide-team" role="img" aria-label="Smiling advisors reviewing documents with a client"></div>
  <div class="abs hero-caption"><h1>QRV Services Are Offered By Industry Executives With Extensive M&amp;A Experience</h1></div>
</section>
<svg class="abs hero-curve" width="1028" height="406" viewBox="0 0 1028 406">
  <path d="M0,406 Q514,318 1028,406 Z" fill="#f3f3f3"/>
  <path d="M0,406 Q514,318 1028,406" fill="none" stroke="#1e1e1e" stroke-width="2"/>
</svg>
<div class="abs dots"><span class="on"></span><span></span><span></span><span></span></div>

<div class="abs title-rule" style="left:204px"></div>
<h2 class="abs section-title">Our Services</h2>
<div class="abs title-rule" style="left:604px"></div>

<article class="abs service" style="left:119px">
  <div class="service-head accent">
    <h2>Business<br>Planning</h2>
    <svg width="60" height="72" viewBox="0 0 60 72"><path d="M4 72V4h46v46" fill="none" stroke="#fff" stroke-width="3"/><path d="M12 16h30M12 26h30M12 36h30M12 46h18" stroke="#fff" stroke-width="3"/><path d="M30 58l8 8 18-20" fill="none" stroke="#fff" stroke-width="4"/></svg>
  </div>
  <p>Lorem ipsum dolor sit amet, consectetuer eadi pis elit, sed diam nonummy nibh euismod tinc idunt ut laoreeio dolore magna aliquam erate</p>
</article>
<article class="abs service" style="left:394px">
  <div class="service-head">
    <h2>Mergers &amp;<br>Acquisition</h2>
    <svg width="70" height="60" viewBox="0 0 70 60"><circle cx="25" cy="32" r="15" fill="none" stroke="#fff" stroke-width="4"/><circle cx="45" cy="32" r="15" fill="none" stroke="#fff" stroke-width="4"/></svg>
  </div>
  <p>Lorem ipsum dolor sit amet, consectetuer eadi pis elit, sed diam nonummy nibh euismod tinc idunt ut laoreeio dolore magna aliquam erate</p>
</article>
<article class="abs service" style="left:670px">
  <div class="service-head">
    <h2>Advisory<br>Services</h2>
    <svg width="60" height="60" viewBox="0 0 60 60"><path d="M10 6h44v28H30l-8 8v-8H10z" fill="none" stroke="#fff" stroke-width="3"/><path d="M18 15h28M18 22h28" stroke="#fff" stroke-width="2.5"/></svg>
  </div>
  <p>Lorem ipsum dolor sit amet, consectetuer eadi pis elit, sed diam nonummy nibh euismod tinc idunt ut laoreeio dolore magna aliquam erate</p>
</article>
<div class="abs band-shadow"></div>

<section class="abs panel" style="left:122px">
  <h3 class="panel-head">
    <svg width="20" height="16" viewBox="0 0 20 16" fill="#fff"><circle cx="10" cy="4" r="3.2"/><circle cx="4" cy="6" r="2.5"/><circle cx="16" cy="6" r="2.5"/><path d="M4 16c0-4 2.5-7 6-7s6 3 6 7zM0 15c0-3 1.5-5 4-5l1 .3C3.8 11.5 3 13 3 15zM20 15c0-3-1.5-5-4-5l-1 .3c1.2 1.2 2 2.7 2 4.7z"/></svg>
    ABOUT QRV
  </h3>
  <div class="about-photo" role="img" aria-label="Three colleagues in conversation at the office"></div>
  <p class="about-text">QRV assists business owners within the logistics industry to implement growth and exit strategies. We offer business planning and merger and acquisition (M&amp;A) advisory services.</p>
  <span class="more">Read More »</span>
</section>

<section class="abs panel" style="left:394px">
  <h3 class="panel-head">
    <svg width="16" height="16" viewBox="0 0 16 16"><rect x="1" y="2" width="14" height="13" fill="none" stroke="#fff" stroke-width="1.5"/><path d="M1 6h14" stroke="#fff" stroke-width="1.5"/><path d="M4 9h2M7 9h2M10 9h2M4 12h2M7 12h2M10 12h2" stroke="#fff" stroke-width="1.5"/></svg>
    NEWS &amp; EVENTS
  </h3>
  <div class="news-item" style="top:60px"><div class="date"><b>Apr</b><i>02</i></div><p><strong>Lorem ipsum dolor sit amet, consectetue</strong> eadi pis elit, sed diam nonummy nibherini euismod tinc idunt ut laoreeio.</p></div>
  <div class="news-item" style="top:108px"><div class="date"><b>Apr</b><i>03</i></div><p><strong>Lorem ipsum dolor sit amet, consectetue</strong> eadi pis elit, sed diam nonummy nibherini euismod tinc idunt ut laoreeio.</p></div>
  <div class="news-item" style="top:156px"><div class="date"><b>Apr</b><i>04</i></div><p><strong>Lorem ipsum dolor sit amet, consectetue</strong> eadi pis elit, sed diam nonummy nibherini euismod tinc idunt ut laoreeio.</p></div>
  <span class="more">Read More »</span>
</section>

<section class="abs panel" style="left:664px">
  <h3 class="panel-head">
    <svg width="16" height="16" viewBox="0 0 16 16"><path d="M2 2h8M2 2v13h11V9" fill="none" stroke="#fff" stroke-width="1.5"/><path d="M6 11l1-3 6-6 2 2-6 6z" fill="#fff"/></svg>
    QUICK CONTACT
  </h3>
  <div class="field" style="top:59px">Name</div>
  <div class="field" style="top:88px">Email</div>
  <div class="field" style="top:116px">Phone</div>
  <div class="field" style="top:144px;height:52px">Message</div>
  <div class="submit">Submit</div>
</section>

<footer class="abs footer">
  <h3 style="left:118px;top:18px">Quick Links</h3>
  <div class="f-rule" style="left:118px;top:42px;width:104px"></div>
  <ul class="quick-links">
    <li>Home</li><li>About Us</li><li>Consulting Services</li><li>News &amp; Events</li><li>FAQ's</li><li>Contact Us</li>
  </ul>
  <div class="f-divider" style="left:254px"></div>

  <h3 style="left:288px;top:18px">Contact Us</h3>
  <div class="f-rule" style="left:288px;top:42px;width:376px"></div>
  <div class="map" role="img" aria-label="Street map showing the office location"></div>
  <div class="contact-row" style="top:54px">
    <svg width="16" height="14" viewBox="0 0 16 14" fill="#fff"><path d="M8 0l8 7h-2v7h-4V9H6v5H2V7H0z"/></svg>
    <span>Lorem ipsum dolor sit amet, conse<br>adipiscing elit, sed diam nonummy.</span>
  </div>
  <div class="contact-row" style="top:93px">
    <svg width="16" height="16" viewBox="0 0 16 16"><circle cx="8" cy="8" r="7" fill="none" stroke="#fff" stroke-width="1.3"/><path d="M5.5 4.5c-.6.6-.8 1.5-.3 2.8s1.7 2.7 3.1 3.4c.9.4 1.6.2 2.2-.5l-1.3-1.2-.9.6c-.8-.5-1.6-1.2-2-2.1l.6-.9z" fill="#fff"/></svg>
    <span>123.456.7890</span>
  </div>
  <div class="contact-row" style="top:119px">
    <svg width="16" height="16" viewBox="0 0 16 16"><text x="8" y="13" text-anchor="middle" font-size="15" fill="#fff" font-family="Ubuntu,sans-serif">@</text></svg>
    <span>info@qrvadvisors-example.com</span>
  </div>
  <div class="f-divider" style="left:700px"></div>

  <div class="footer-mark">QRV</div>
  <div class="social-foot" aria-label="Social links"><span></span><span></span><span></span></div>
  <p class="copyright">© 2014 qrvadvisors-example.&nbsp; All Rights Reserved .</p>
</footer>

</body>
</html>
```